Home Security Company Business Card

Looking for a eye catching business card that is non traditional and stands out but yet still looks professional. It should include all the pertinent information such as name, title, address, telephone, e-mail, website address should definitely stand out and then finally the logo.

Target Market(s)

Residential and Commercial accounts mostly upscale accounts

Industry/Entity Type

Security

Contact Information for Business Card

Name
Title
Address
Office #
Cell #
E-mail
Website

Font styles to use
Serif
Sans Serif

Requirements
Must have
• Logo, two sided color configuration
Nice to have
• You decide
Should not have
• There really aren't any.

```html
<!DOCTYPE html>
<html lang="en">
<head>
<meta charset="utf-8">
<title>Ironvale Security Systems Inc. – Business Card</title>
<link rel="stylesheet" href="https://fonts.googleapis.com/css2?family=Open+Sans:wght@400;600;700&display=swap">
<style>
  :root {
    --maroon: #7a1a22;
    --maroon-dark: #5e1118;
    --gold: #d9a43a;
    --card: #ffffff;
    --backdrop: #e9e4df;
    --ink: #2b1a1a;
  }
  * { margin: 0; padding: 0; box-sizing: border-box; }
  html, body { width: 1200px; height: 913px; overflow: hidden; }
  body {
    background: var(--backdrop);
    font-family: "Open Sans", Arial, sans-serif;
    position: relative;
  }
  .card {
    position: absolute;
    width: 560px;
    height: 320px;
    background: var(--card);
    border-radius: 14px;
    overflow: hidden;
    box-shadow: 0 10px 28px rgba(60, 30, 20, 0.18);
  }
  .card--front { left: 50px; top: 110px; }
  .card--back { left: 590px; top: 480px; }

  .band {
    position: absolute;
    top: 0; bottom: 0;
    width: 44px;
    background: linear-gradient(90deg, var(--maroon-dark), var(--maroon));
  }
  .card--front .band { left: 0; }
  .card--back .band { right: 0; }

  .contact-icons {
    position: absolute;
    left: 0; bottom: 30px;
    width: 44px;
    display: flex;
    flex-direction: column;
    align-items: center;
    gap: 8px;
  }
  .contact-icons svg { width: 14px; height: 14px; }

  .brand {
    display: flex;
    align-items: center;
    gap: 10px;
    color: var(--maroon);
    font-weight: 600;
    text-transform: uppercase;
    letter-spacing: 0.04em;
  }
  .brand__mark {
    background: var(--gold);
    flex: none;
  }
  .brand__name { line-height: 1.1; }

  .card--front .brand {
    position: absolute;
    left: 72px; top: 42px;
    font-size: 15px;
  }
  .card--front .brand__mark { width: 22px; height: 22px; }

  .person {
    position: absolute;
    left: 72px; top: 132px;
  }
  .person__name {
    font-size: 27px;
    font-weight: 700;
    color: var(--maroon);
    line-height: 1.1;
  }
  .person__title {
    font-size: 15px;
    color: var(--gold);
    margin-bottom: 14px;
  }
  .person__line {
    font-size: 15px;
    font-weight: 600;
    color: var(--ink);
    line-height: 1.4;
  }

  .card--back .brand {
    position: absolute;
    left: 0; right: 44px; top: 110px;
    justify-content: center;
    font-size: 22px;
  }
  .card--back .brand__mark { width: 30px; height: 30px; }
  .tagline {
    position: absolute;
    left: 0; right: 44px; top: 214px;
    text-align: center;
    font-size: 16px;
    font-weight: 700;
    color: var(--maroon);
    letter-spacing: 0.03em;
    text-transform: uppercase;
  }
</style>
</head>
<body>
  <section class="card card--front" aria-label="Business card front">
    <div class="band">
      <div class="contact-icons">
        <svg viewBox="0 0 16 16" aria-hidden="true"><path d="M4 1.5l2 3-1.3 1.4a8 8 0 0 0 5.4 5.4L11.5 10l3 2-1 2.5C7 14 2 9 1.5 2.5z" fill="var(--gold)"/></svg>
        <svg viewBox="0 0 16 16" aria-hidden="true"><rect x="4.5" y="1" width="7" height="14" rx="1.5" fill="none" stroke="var(--gold)" stroke-width="1.5"/><circle cx="8" cy="12.5" r="0.9" fill="var(--gold)"/></svg>
        <svg viewBox="0 0 16 16" aria-hidden="true"><rect x="1.5" y="3.5" width="13" height="9" fill="none" stroke="var(--gold)" stroke-width="1.4"/><path d="M1.5 3.5L8 9l6.5-5.5" fill="none" stroke="var(--gold)" stroke-width="1.4"/></svg>
        <svg viewBox="0 0 16 16" aria-hidden="true"><circle cx="8" cy="8" r="6.3" fill="none" stroke="var(--gold)" stroke-width="1.3"/><ellipse cx="8" cy="8" rx="2.8" ry="6.3" fill="none" stroke="var(--gold)" stroke-width="1.1"/><path d="M1.7 8h12.6M2.8 4.8h10.4M2.8 11.2h10.4" stroke="var(--gold)" stroke-width="1"/></svg>
      </div>
    </div>

    <div class="brand">
      <span class="brand__mark"></span>
      <span class="brand__name">Ironvale Security Systems Inc.</span>
    </div>

    <div class="person">
      <p class="person__name">Daniel Harwick</p>
      <p class="person__title">Owner</p>
      <p class="person__line">+330 2555-0142</p>
      <p class="person__line">+3302555-01873</p>
      <p class="person__line">info@danielharwickmail.com</p>
      <p class="person__line">www.ironvalesecuritysystemsinc.com</p>
    </div>
  </section>

  <section class="card card--back" aria-label="Business card back">
    <div class="band"></div>
    <div class="brand">
      <span class="brand__mark"></span>
      <span class="brand__name">Ironvale Security Systems Inc.</span>
    </div>
    <p class="tagline">Protect what matters most</p>
  </section>
</body>
</html>
```